Application for baby milk and water counter

We are building baby food app. Need to design main screen for tha app first so we can go forward to other secondary screens of the app

Food dashboard screen
Food dashboard screen is main page for view/edit food data

General vision
I see the app in pastel colors with some illustrations to make the app more in positive. You can influence from game Glimmer Tides. I see with smooth colors and gradients like in a game. Also need to have animations/transitions for each action. Each click should create smooth transition to new state. My idea is to build one dashboard screen for food which we can reuse it for other screens. So a lot of thinking should go into design stage to app appealing.

Food Dashboard
Current screen should show all the data about food intake of the baby. So here user should see

Milk How much food baby had in ml/oz. So there should be some kind of illustrated bottle or glass or smth that shows it is filled with that amount.

Add/Remove controls for food. Should be some kind of custom control for inputing amount to remove/add. I see it as a slider on the side of the bottle. User slides up or down and amount is added/removed.

Notification. So user should be aware how many hours/minutes left for next food intake. This is optional field, so consider it could be disabled. So no empty space should be on a screen. There should be human readable text. Something like. 1:30 minutes left for next intake. Maybe could be some custom made icons to illustrate that it is next food intake.

Burped: User should have ability to how much baby burped. This amount is integer value. So it could be “Baby burped 2 times today”. So again here I see some custom made/icon to illustrate how many times baby burped and amount next to it. I see changing the value just by tapping, but I don’t know how to edit if user tapped accidentally more than it should be. So TBD here.

Date and time: Dashboard should show for which date it is viewing/editing data. Should be able to change it, so user can add/edit data for yesterday. Don’t want to see here calendar on a screen so need to come up with nice design decision.

Water: User should have ability to view/edit water intake of the baby, but water is secondary information so it should be smaller than milk, or come up with some other idea how to show the water. I see to have same controls for water like for milk. Water intake is optional it can be disabled by the user.

Target Market(s)

For just became mothers

Font styles to use
Sans Serif

Colors
0094D4
00A9DD
6FCCEA
C7EBF8
E9F6FB
FFC000
F8CF3A
FAE287
FDF2CF
FEFAEE
E54698
E96AAD
F1A4CE
F9D9EA
FCEFF6

Requirements
Must have
• Ilustrations or playfull icons for show information

```html
<!DOCTYPE html>
<html lang="en">
<head>
<meta charset="utf-8">
<title>Baby App – Food Dashboard</title>
<link href="https://fonts.googleapis.com/css2?family=Gelasio&family=Josefin+Sans:wght@400;600;700&family=Nunito:wght@900&family=Roboto:wght@400&display=swap" rel="stylesheet">
<style>
  :root{
    --page:#f2f2f2;
    --blue-deep:#0094d4;
    --blue:#00a9dd;
    --blue-mid:#6fccea;
    --blue-light:#c7ebf8;
    --blue-pale:#e9f6fb;
    --scale:#5b9fe6;
    --navy:#2a3a9e;
    --marker:#3a4aa8;
    --ink:#1a1a1a;
    --white:#ffffff;
  }
  *{box-sizing:border-box;margin:0;padding:0}
  html,body{width:1200px;height:1041px;overflow:hidden;background:var(--page)}
  body{position:relative;font-family:"Josefin Sans",sans-serif}
  .screen{
    position:absolute;left:354px;top:80px;width:491px;height:873px;overflow:hidden;
    background:linear-gradient(180deg,#b5e4f6 0%,#9fdaf1 45%,var(--blue-mid) 100%);
  }
  .app-bar{
    position:absolute;left:0;top:0;width:100%;height:50px;
    background:linear-gradient(180deg,var(--blue) 0%,var(--blue-deep) 100%);
    display:flex;align-items:center;padding:0 17px;color:var(--white);
  }
  .app-bar .menu{width:25px;height:20px}
  .app-bar .title{font-family:"Gelasio",serif;font-size:20px;margin-left:15px;flex:1}
  .app-bar .settings{width:28px;height:28px}
  .date-band{
    position:absolute;left:0;top:50px;width:100%;height:84px;
    background:linear-gradient(180deg,var(--blue-light) 0%,#b4e4f6 100%);
  }
  .day{
    position:absolute;left:20px;top:28px;font-family:"Nunito",sans-serif;font-weight:900;
    font-size:27px;color:var(--blue-deep);letter-spacing:.3px
  }
  .month-year{
    position:absolute;right:29px;top:22px;text-align:right;font-size:17px;line-height:20px;color:var(--ink)
  }
  .milk-bottle{
    position:absolute;left:75px;top:182px;width:143px;height:395px;
    border-radius:40px 40px 32px 32px;
    background:linear-gradient(180deg,#dfeef3 0%,#d6e9f0 45%,#f1ece3 46.5%,#f4f0ea 75%,#ffffff 100%);
    box-shadow:0 10px 18px rgba(0,70,110,.25);
  }
  .water-bottle{
    position:absolute;left:305px;top:287px;width:86px;height:286px;
    border-radius:30px 30px 14px 14px;
    background:linear-gradient(180deg,#c9e7f5 0%,#b8def1 65.7%,var(--navy) 65.7%,var(--navy) 100%);
    box-shadow:0 10px 16px rgba(0,70,110,.25);
  }
  .scale{position:absolute;left:0;top:0;width:100%;height:100%;pointer-events:none;font-family:"Roboto",sans-serif;color:var(--scale)}
  .scale .rule{position:absolute;width:1px;background:var(--scale)}
  .scale .marker{position:absolute;height:5px;border-radius:3px;background:var(--marker)}
  .scale .mark{position:absolute;transform:translateY(-50%);white-space:nowrap;line-height:1}
  .milk-scale .mark{font-size:12px}
  .water-scale .mark{font-size:9px}
  .toggle-off{
    position:absolute;left:313px;top:222px;width:70px;height:36px;border-radius:18px;
    background:rgba(233,246,251,.75);display:flex;align-items:center;padding:0 6px 0 13px;
    font-size:10px;color:var(--ink);justify-content:space-between
  }
  .toggle-off .knob{width:22px;height:22px;border-radius:50%;background:var(--white)}
  .pill{
    position:absolute;left:53px;width:387px;height:74px;border-radius:37px;display:flex;align-items:center
  }
  .burp-counter{
    top:651px;background:linear-gradient(180deg,var(--blue) 0%,var(--blue-deep) 100%);
    color:var(--white);padding:0 26px;justify-content:space-between
  }
  .burp-counter .label{display:flex;align-items:center;gap:12px;font-weight:700;font-size:18px;letter-spacing:.6px;padding-top:3px}
  .burp-counter .step{width:22px;height:22px}
  .burp-counter .wind{width:30px;height:30px;margin-top:-3px}
  .next-intake{top:754px;background:var(--white);padding:0 20px 0 20px}
  .next-intake .bell{width:26px;height:28px}
  .next-intake .text{font-size:17px;color:var(--ink);margin-left:14px;flex:1;padding-top:3px;letter-spacing:.3px}
  .toggle-on{
    width:70px;height:36px;border-radius:18px;background:var(--blue-mid);display:flex;align-items:center;
    padding:0 13px 0 6px;justify-content:space-between;font-size:10px;font-weight:600;color:var(--white)
  }
  .toggle-on .knob{width:22px;height:22px;border-radius:50%;background:var(--white)}
</style>
</head>
<body>
  <main class="screen">
    <header class="app-bar">
      <svg class="menu" viewBox="0 0 25 20" aria-hidden="true"><g stroke="#fff" stroke-width="2.2" stroke-linecap="round"><line x1="1" y1="2" x2="24" y2="2"/><line x1="1" y1="10" x2="24" y2="10"/><line x1="1" y1="18" x2="24" y2="18"/></g></svg>
      <span class="title">Baby App</span>
      <svg class="settings" viewBox="0 0 24 24" aria-hidden="true"><g fill="none" stroke="#fff" stroke-width="1.5"><circle cx="12" cy="12" r="3.3"/><path d="M12 2.5l1.6 2.3 2.7-.7.7 2.7 2.6.9-.6 2.7 1.9 2-1.9 2 .6 2.7-2.6.9-.7 2.7-2.7-.7L12 21.5l-1.6-2.3-2.7.7-.7-2.7-2.6-.9.6-2.7-1.9-2 1.9-2-.6-2.7 2.6-.9.7-2.7 2.7.7z"/></g></svg>
    </header>

    <section class="date-band">
      <h1 class="day">FRIDAY 02</h1>
      <p class="month-year">JUNE<br>2023</p>
    </section>

    <div class="milk-bottle" role="img" aria-label="Illustrated baby bottle filled with milk to about 140 ml"></div>
    <div class="scale milk-scale" aria-label="Milk scale in oz and ml">
      <span class="rule" style="left:143px;top:337px;height:206px"></span>
      <span class="marker" style="left:137px;top:363px;width:13px"></span>
      <span class="mark" style="left:116px;top:335px">5 -</span>
      <span class="mark" style="left:116px;top:383px">4 -</span>
      <span class="mark" style="left:116px;top:433px">3 -</span>
      <span class="mark" style="left:116px;top:483px">2 -</span>
      <span class="mark" style="left:118px;top:530px">1 -</span>
      <span class="mark" style="left:155px;top:344px">- 150</span>
      <span class="mark" style="left:155px;top:384px">- 125</span>
      <span class="mark" style="left:155px;top:424px">- 100</span>
      <span class="mark" style="left:155px;top:464px">- 75</span>
      <span class="mark" style="left:155px;top:504px">- 50</span>
      <span class="mark" style="left:155px;top:544px">- 25</span>
    </div>

    <div class="toggle-off"><span>OFF</span><span class="knob"></span></div>
    <div class="water-bottle" role="img" aria-label="Illustrated water bottle filled to about 80 ml"></div>
    <div class="scale water-scale" aria-label="Water scale in ml">
      <span class="rule" style="left:344px;top:387px;height:163px"></span>
      <span class="marker" style="left:338px;top:470px;width:13px"></span>
      <span class="mark" style="left:352px;top:391px">- 150</span>
      <span class="mark" style="left:352px;top:423px">- 125</span>
      <span class="mark" style="left:352px;top:455px">- 100</span>
      <span class="mark" style="left:352px;top:486px">- 75</span>
      <span class="mark" style="left:352px;top:518px">- 50</span>
      <span class="mark" style="left:352px;top:549px">- 25</span>
    </div>

    <div class="pill burp-counter">
      <svg class="step" viewBox="0 0 22 22" aria-label="Decrease"><circle cx="11" cy="11" r="10" fill="none" stroke="#fff" stroke-width="1.4"/><line x1="6" y1="11" x2="16" y2="11" stroke="#fff" stroke-width="1.4"/></svg>
      <span class="label">
        <svg class="wind" viewBox="0 0 30 30" aria-hidden="true"><g fill="none" stroke="#fff" stroke-width="1.5" stroke-linecap="round"><path d="M9 12a6 6 0 0 1 12 0"/><line x1="15" y1="3" x2="15" y2="5"/><path d="M3 15h19a3 3 0 1 1-3 3"/><path d="M2 19h13"/><path d="M5 23h16a3 3 0 1 1-3 3"/><line x1="24" y1="15" x2="28" y2="15"/></g></svg>
        2 TIMES BURPED
      </span>
      <svg class="step" viewBox="0 0 22 22" aria-label="Increase"><circle cx="11" cy="11" r="10" fill="none" stroke="#fff" stroke-width="1.4"/><line x1="6" y1="11" x2="16" y2="11" stroke="#fff" stroke-width="1.4"/><line x1="11" y1="6" x2="11" y2="16" stroke="#fff" stroke-width="1.4"/></svg>
    </div>

    <div class="pill next-intake">
      <svg class="bell" viewBox="0 0 26 28" aria-hidden="true"><g fill="none" stroke="#6fccea" stroke-width="1.5" stroke-linejoin="round"><path d="M13 3a8 8 0 0 1 8 8v7l3 4H2l3-4v-7a8 8 0 0 1 8-8z"/><path d="M10 24a3 3 0 0 0 6 0"/><line x1="13" y1="1" x2="13" y2="3"/></g></svg>
      <span class="text">2 Hours Left for Next Intake</span>
      <div class="toggle-on"><span class="knob"></span><span>ON</span></div>
    </div>
  </main>
</body>
</html>
```